verdant terraces simple classy business card design

my name is colin barrow and I run a gardening business aimed at high class verdant terraces. the business name is verdant terraces and our logo was designed on pixel harbour .My clientel are anything from residential homes to businesses. I take pride in my work and know that I offer a service like no other in my area.
The business card will be used to represent my business and I want it to be not only rememberable, but simplistic and modern. Eye catching too. Of course I would like it relatable to gardening and appealing to the correct clientel - those being garden enthusiasts, prestigious homes and businesses that are after top of the line gardening services like no other on the market.
I am not a typical lawn mowing business so I don't want a typical card design that represents that. The gardens I work with are generally million dollar properties with owners who are very garden proud looking for upkeep and guidance from me along with sometimes whole new garden designs. I want the business cards to show to my clients that I take pride, as they do, in their garden. And I want them to know from my card that I am a professional, qualified horticulturist offering them a top of the line service for life. I want them to refer my business on. I want them to look at my business card and see class and professionalism in a modern unique bold way.
The card should be simple with the possibility of the logo on the front being embossed/debossed and my details on the back the card should have a organic garden feel it's very important to me that it is absolutely perfect
I am also very open to ideas and suggestions so look forward to seeing the designs. the business logo has been supplied with this project and I want the card to be double sided

Contact info is
Colin Barrow - Managing Director / Horticulturist
Phone : 0481 526 704
Email: colinbarrow@verdantterraces.example.au

Target Market(s)

high class gardens residential and commercial

Industry/Entity Type

Gardener

Contact Information for Business Card

Contact info is
Phone : 0481 526 704

PLEASE MAKE CARD DOUBLE SIDED

Requirements
Must have
• organic simple classy modern feel
• must flow with the current logo that has been supplied with this project
• Double sided
• Must explain in a simple way that I deal with high end gardens and I'm a qualified horticulturist
Nice to have
• embossed debossed logo
Should not have
• shouldn't be to busy or cheap looking

```html
<!DOCTYPE html>
<html lang="en">
<head>
<meta charset="utf-8">
<title>Verdant Terraces – Business Card</title>
<link rel="stylesheet" href="https://fonts.googleapis.com/css2?family=Arimo:wght@400;700&display=swap">
<style>
  :root {
    --backdrop: #959696;
    --card-stock: #eceded;
    --brand-green: #4f8743;
    --band-green: #558a47;
    --band-text: #ffffff;
    --band-text-soft: #eef3ec;
  }
  * { box-sizing: border-box; margin: 0; padding: 0; }
  html, body {
    width: 1105px;
    height: 1200px;
    overflow: hidden;
    background: var(--backdrop);
    font-family: "Arimo", Arial, sans-serif;
  }
  .card {
    position: absolute;
    left: 182px;
    width: 746px;
    height: 427px;
    background: var(--card-stock);
  }
  .card--front { top: 119px; }
  .card--back  { top: 635px; }

  .brand {
    position: absolute;
    left: 0;
    width: 100%;
    display: flex;
    flex-direction: column;
    align-items: center;
  }
  .card--front .brand { top: 36px; }
  .card--back  .brand { top: 114px; }

  .brand__dot {
    width: 104px;
    height: 104px;
    border-radius: 50%;
    background: var(--brand-green);
  }
  .brand__name {
    margin-top: 22px;
    color: var(--brand-green);
    font-weight: 700;
    font-size: 34px;
    letter-spacing: 4px;
    text-transform: uppercase;
    line-height: 1;
  }

  .contact-band {
    position: absolute;
    left: 0;
    top: 251px;
    width: 100%;
    height: 176px;
    background: var(--band-green);
    color: var(--band-text);
    text-align: center;
  }
  .contact-band__name {
    margin-top: 26px;
    font-size: 24px;
    font-weight: 700;
    line-height: 1.2;
  }
  .contact-band__role {
    margin-top: 4px;
    font-size: 19px;
    color: var(--band-text-soft);
  }
  .contact-band__details {
    margin-top: 18px;
    font-size: 16.5px;
    color: var(--band-text-soft);
  }
  .contact-band__details b { font-weight: 700; color: var(--band-text); }
  .contact-band__details .gap { display: inline-block; width: 14px; }
  .contact-band__web {
    margin-top: 10px;
    font-size: 19px;
    letter-spacing: 2.4px;
    font-weight: 700;
  }
</style>
</head>
<body>
  <section class="card card--front">
    <div class="brand">
      <div class="brand__dot"></div>
      <div class="brand__name">Verdant Terraces</div>
    </div>
    <div class="contact-band">
      <p class="contact-band__name">Colin Barrow</p>
      <p class="contact-band__role">Managing Director / Horticulturist</p>
      <p class="contact-band__details"><b>P :</b> 0481 526 704<span class="gap"></span><b>E :</b> colinbarrow@verdantterraces.example.au</p>
      <p class="contact-band__web">verdantterraces.example.au</p>
    </div>
  </section>

  <section class="card card--back">
    <div class="brand">
      <div class="brand__dot"></div>
      <div class="brand__name">Verdant Terraces</div>
    </div>
  </section>
</body>
</html>
```